Presentation for partners template design for a healthy bakery

A bakery that makes healthy homemade cupcakes, needs a presentation template for wholesale partners. We need 3-4 template pages with pictures and text blocks, one template that can accomodate a pricing table. Just to give you an idea for the templates our final presentation will include:
1. Cover page with logo
2. Intro page about us
3. Detailed description of products
4. Menu table: cupcakes with wholesale pricing
5. Contact page
Updates

Project Deadline Extended Reason: We feel we needed to extend the deadline to have more time to discuss and to give proper feedback to designers Added Tuesday, May 23, 2017

Target Market(s)

Food stores, cafés, fitness clubs, pastry shops, etc.

Industry/Entity Type

Bakery

Font styles to use
Sans Serif

Colors
fee3d4
fce8d3
eaf2ce
cadf82
ffffff
000000
cfeae6
ec1f27
86cfc6

Requirements
Must have
• Presentation needs to look serious and professional. The design needs to give an eco feel: we use recycled materials in our packaging and production. Please make sure the fonts you use support Cyrillic.
Nice to have
• The format of pages is either square or horizontal A4. The company mint colour (see logo attached) needs to be used, but other colours can be used in addition (lime green, peach, black, chocolate brown, red, etc). Craft paper texture (like our packaging, see photos) would be nice to have.

```html
<!DOCTYPE html>
<html lang="en">
<head>
<meta charset="utf-8">
<title>Menu</title>
<link href="https://fonts.googleapis.com/css2?family=Dosis:wght@300;400&display=swap" rel="stylesheet">
<style>
  :root {
    --mint: #cfeae6;
    --lime: #cadf82;
    --white: #ffffff;
    --ink: #000000;
    --photo-dark: #3a3430;
    --photo-mid: #5d5048;
    --photo-teal: #4f6f68;
  }
  html, body {
    margin: 0;
    padding: 0;
    width: 1200px;
    height: 848px;
    overflow: hidden;
    background: var(--white);
  }
  .page {
    position: relative;
    width: 1200px;
    height: 848px;
    background: var(--white);
    font-family: "Dosis", sans-serif;
    overflow: hidden;
  }
  .side-visual {
    position: absolute;
    left: 0;
    top: 0;
    width: 532px;
    height: 848px;
    display: block;
  }
  .accent-band {
    position: absolute;
    left: 1091px;
    top: 0;
    width: 109px;
    height: 848px;
    background: var(--lime);
  }
  .menu-title {
    position: absolute;
    left: 714px;
    top: 138px;
    width: 190px;
    margin: 0;
    font-weight: 300;
    font-size: 88px;
    line-height: 1;
    letter-spacing: 1px;
    color: var(--lime);
    text-align: center;
  }
  .menu-list {
    position: absolute;
    left: 714px;
    top: 289px;
    margin: 0;
    padding: 0;
    list-style: none;
  }
  .menu-item {
    font-weight: 400;
    font-size: 18.5px;
    line-height: 34.25px;
    color: var(--ink);
    white-space: nowrap;
  }
</style>
</head>
<body>
<main class="page">
  <svg class="side-visual" viewBox="0 0 532 848" xmlns="http://www.w3.org/2000/svg">
    <defs>
      <linearGradient id="photoTone" x1="0" y1="0" x2="1" y2="1">
        <stop offset="0" stop-color="var(--photo-mid)"/>
        <stop offset="0.45" stop-color="var(--photo-dark)"/>
        <stop offset="1" stop-color="var(--photo-teal)"/>
      </linearGradient>
    </defs>
    <rect class="mint-band" x="0" y="0" width="532" height="848" fill="var(--mint)"/>
    <path role="img" aria-label="Photo of decorated homemade cupcakes on a mint gingham napkin"
          d="M0 0 H416 C412 130 398 260 404 384 C410 520 430 680 432 848 H0 Z"
          fill="url(#photoTone)"/>
  </svg>

  <div class="accent-band"></div>

  <h1 class="menu-title">MENU</h1>
  <ul class="menu-list">
    <li class="menu-item">Cupcake -----------10$</li>
    <li class="menu-item">Cupcake -----------10$</li>
    <li class="menu-item">Cupcake -----------10$</li>
    <li class="menu-item">Cupcake -----------10$</li>
    <li class="menu-item">Cupcake -----------10$</li>
    <li class="menu-item">Cupcake -----------10$</li>
    <li class="menu-item">Cupcake -----------10$</li>
    <li class="menu-item">Cupcake -----------10$</li>
    <li class="menu-item">Cupcake -----------10$</li>
    <li class="menu-item">Cupcake -----------10$</li>
    <li class="menu-item">Cupcake -----------10$</li>
    <li class="menu-item">Cupcake -----------10$</li>
    <li class="menu-item">Cupcake -----------10$</li>
  </ul>
</main>
</body>
</html>
```